Veldmark Supplies Business Card

Professional business card that stand out to our potential customers. Front and back with clean modern design

Industry/Entity Type

Oil and gas

Contact Information for Business Card

Name, address, website , office phone and cell number

Requirements
Must have
• Editable files for each employee

```html
<!DOCTYPE html>
<html lang="en">
<head>
<meta charset="utf-8">
<title>Veldmark Supplies Business Card</title>
<link rel="stylesheet" href="https://fonts.googleapis.com/css2?family=Poppins:wght@400;500;700&display=swap">
<style>
  :root {
    --page-bg: #2b2b2b;
    --card-bg: #1d1d1f;
    --card-edge: #121213;
    --brand-red: #ee1d25;
    --brand-blue: #12a8d3;
    --ink-light: #f2f2f2;
    --ink-muted: #c9c9c9;
    --pattern-light: #bdbdbd;
    --pattern-mid: #4a4a4a;
    --pattern-dark: #0d0d0d;
  }
  * { box-sizing: border-box; margin: 0; padding: 0; }
  html, body {
    width: 1200px; height: 875px; overflow: hidden;
    background: var(--page-bg);
    font-family: "Poppins", sans-serif;
  }
  .sheet {
    position: relative; width: 1200px; height: 875px;
    display: flex; align-items: center; justify-content: center; gap: 60px;
  }
  .card {
    position: relative; width: 520px; height: 298px;
    border-radius: 16px; overflow: hidden;
    background: var(--card-bg);
    box-shadow: 0 18px 40px rgba(0,0,0,.45);
  }

  /* Back */
  .card-back .pattern-field {
    position: absolute; inset: 0;
    background: linear-gradient(115deg, var(--pattern-light) 0%, var(--pattern-mid) 38%, var(--pattern-dark) 75%, #050505 100%);
  }
  .card-back .center-mark {
    position: absolute; left: 50%; top: 50%; transform: translate(-50%, -50%);
    display: flex; align-items: center; gap: 10px;
    padding: 12px 18px; border-radius: 6px;
    background: var(--card-bg);
  }
  .center-mark .mark-square { width: 14px; height: 14px; background: var(--brand-red); }
  .center-mark .mark-name {
    color: var(--ink-light); font-weight: 700; font-size: 20px;
    text-transform: uppercase; letter-spacing: .04em;
  }

  /* Front */
  .card-front .brand-lockup {
    position: absolute; left: 44px; top: 66px;
    display: flex; align-items: center; gap: 12px;
  }
  .brand-lockup .mark-square { width: 22px; height: 22px; background: var(--brand-red); }
  .brand-lockup .mark-name {
    color: var(--ink-light); font-weight: 700; font-size: 28px;
    text-transform: uppercase; letter-spacing: .04em;
  }
  .card-front .identity {
    position: absolute; left: 44px; top: 140px; width: 205px;
    text-align: right;
  }
  .identity .person-name { color: var(--brand-red); font-weight: 700; font-size: 20px; line-height: 1.15; }
  .identity .person-title { color: var(--ink-light); font-size: 11px; line-height: 1.5; }
  .identity .address { color: var(--ink-light); font-size: 11px; line-height: 1.45; }
  .card-front .divider {
    position: absolute; left: 266px; top: 140px; width: 1px; height: 88px;
    background: var(--ink-muted);
  }
  .card-front .contact-list {
    position: absolute; left: 282px; top: 140px; list-style: none;
  }
  .contact-list li {
    display: flex; align-items: center; gap: 8px;
    color: var(--ink-light); font-size: 11px; line-height: 22px;
  }
  .contact-list svg { width: 11px; height: 11px; fill: var(--brand-red); flex: none; }
  .card-front .edge-band {
    position: absolute; left: 0; right: 0; bottom: 0; height: 9px;
  }
</style>
</head>
<body>
<main class="sheet">

  <section class="card card-back" aria-label="Card back">
    <div class="pattern-field" role="img" aria-label="Repeating embossed brand pattern fading from silver to black"></div>
    <div class="center-mark">
      <span class="mark-square"></span>
      <span class="mark-name">Veldmark Supplies</span>
    </div>
  </section>

  <section class="card card-front" aria-label="Card front">
    <div class="brand-lockup">
      <span class="mark-square"></span>
      <span class="mark-name">Veldmark Supplies</span>
    </div>

    <div class="identity">
      <p class="person-name">Marcus Holt</p>
      <p class="person-title">President</p>
      <p class="address">412 N.Ridgeline Suite 5<br>Midland, Tx 79701</p>
    </div>

    <div class="divider"></div>

    <ul class="contact-list">
      <li>
        <svg viewBox="0 0 12 12" aria-hidden="true"><path d="M1 4c0-2 1-3 3-3h4c2 0 3 1 3 3v1H8V4H4v1H1zM2 6h8l1 5H1z"/></svg>
        (555)204-0391
      </li>
      <li>
        <svg viewBox="0 0 12 12" aria-hidden="true"><path d="M3 0h6a1 1 0 0 1 1 1v10a1 1 0 0 1-1 1H3a1 1 0 0 1-1-1V1a1 1 0 0 1 1-1zm0 2v7h6V2z"/></svg>
        (555)204-0392
      </li>
      <li>
        <svg viewBox="0 0 12 12" aria-hidden="true"><path d="M0 2h12v8H0zm1 1v.5L6 7l5-3.5V3z"/></svg>
        sales@veldmarksupplies.com
      </li>
      <li>
        <svg viewBox="0 0 12 12" aria-hidden="true"><circle cx="6" cy="6" r="6"/></svg>
        www.veldmarksupplies.com
      </li>
    </ul>

    <svg class="edge-band" viewBox="0 0 520 9" preserveAspectRatio="none" aria-hidden="true">
      <polygon points="0,0 330,0 322,9 0,9" fill="var(--brand-red)"/>
      <polygon points="336,0 520,0 520,9 328,9" fill="var(--brand-blue)"/>
    </svg>
  </section>

</main>
</body>
</html>
```